Ledger Lanternfox Powerpoint with Marshal Valorline Type Theme

Need powerpoint template with matching colors and different slide options. Logo and colors to be used can be found at ledgerlanternfox.example. Want brightly colored slide deck that is readable form the back of a room, but highlights colors. I will be incorporating Quizzap into the slides to gamify my presentations.

Target Market(s)

Tech

Industry/Entity Type

IT, specifically database, but crossing over to mental health in IT, important note this is not for a company, this is just for a professional building a brand

Font styles to use
Sans Serif

Colors
0054AA
0677BA
7BADD7
CADEEF
E8F1F8
EB3D1F
EC4F4E
F09395
F8D3D4
FCEDEE

Requirements
Must have
• My Logo in the bottom corner, front page, a thank your page, question page, content page, content page with two columns, content page with graphs, and icons to be used in the primary colors of the logos, About Me Page, Break Slides, Demo break slide
Should not have
• Lighter shades of colors, I want to pop out where colors are used, I want spacing and font size to be readable from the back of a room, most likely black text and white background

```html
<!DOCTYPE html>
<html lang="en">
<head>
<meta charset="utf-8">
<title>Ledger Lanternfox – Marshal Valorline Slide Theme</title>
<link rel="stylesheet" href="https://fonts.googleapis.com/css2?family=Poppins:wght@300;400;500;600;700&display=swap">
<style>
:root{
  --canvas:#dcdcdc;
  --navy:#1d4282;
  --navy-deep:#15366d;
  --red:#e7262d;
  --grey:#8c8c8c;
  --grey-light:#d9d9d9;
  --ink:#3a3a3a;
  --paper:#ffffff;
  --faint:#e3e9f3;
}
*{box-sizing:border-box;margin:0;padding:0}
html,body{width:1200px;height:2500px;overflow:hidden;background:var(--canvas)}
body{font-family:"Poppins",Arial,sans-serif;color:var(--ink)}
.deck{position:relative;width:1200px;height:2500px}
.slide{position:absolute;width:387px;height:217px;background:var(--paper);overflow:hidden}
.slide *{position:absolute}
.slide.navy{background:var(--navy)}
.photo-blue{background:linear-gradient(135deg,#2f5794 0%,#1d4282 55%,#173869 100%)}
.photo-fill{left:0;top:0;width:100%;height:100%}
.brand{font-weight:600;white-space:nowrap;display:flex;align-items:center;gap:4px;position:absolute}
.brand .dot{position:static;display:inline-block;border-radius:50%;background:currentColor;width:1em;height:1em}
.brand.light{color:var(--paper)}
.brand.red{color:var(--red)}
.rail{left:-24px;top:104px;transform:rotate(-90deg);font-size:5.5px;font-weight:600;color:var(--red);white-space:nowrap;width:60px;text-align:center}
.rail.light{color:var(--paper)}
.pageno{left:10px;bottom:6px;font-size:4px;color:var(--grey)}
.title{font-weight:600;color:var(--navy);white-space:nowrap}
.title.light{color:var(--paper)}
.underline{width:16px;height:3px;background:var(--red)}
.body{font-size:4.6px;line-height:1.45;color:var(--ink)}
.body.light{color:var(--paper)}
.centered{text-align:center}
.pill{background:var(--red);color:var(--paper);border-radius:10px;font-weight:600;text-align:center}
.ring-label{font-size:11px;font-weight:500;color:var(--navy)}
.card{border-radius:4px;color:var(--paper);text-align:center}
.card .icon{left:50%;top:-12px;width:24px;height:24px;margin-left:-12px;border-radius:50%;background:var(--paper);border:2px solid currentColor}
.card h4{left:0;right:0;top:20px;font-size:4.6px;font-weight:600}
.card p{left:6px;right:6px;top:30px;font-size:3.8px;line-height:1.4}
.tbl-cell{height:11px;font-size:4px;display:flex;align-items:center;justify-content:center}
.qbox{width:16px;height:16px;border-radius:3px;color:var(--paper);font-weight:700;font-size:9px;display:flex;align-items:center;justify-content:center}
</style>
</head>
<body>
<main class="deck">

<!-- Row 1 -->
<section class="slide" style="left:11px;top:11px">
  <div class="photo-fill photo-blue" role="img" aria-label="Photo of a person working on a tablet, tinted blue"></div>
  <div class="brand light" style="left:140px;top:36px;font-size:9px"><span class="dot"></span>Ledger Lanternfox</div>
  <p class="body light centered" style="left:0;right:0;top:68px;font-size:5px;letter-spacing:1px">www.ledgerlanternfox.example</p>
  <h1 class="title light centered" style="left:0;right:0;top:84px;font-size:23px;line-height:1.05">Presentation<br>Title Goes Here</h1>
  <p class="body light centered" style="left:0;right:0;top:138px;font-size:8px">Sub Title Goes Here</p>
  <div class="pill" style="left:147px;top:177px;width:84px;height:13px;font-size:5px;line-height:13px">Oct 2021</div>
</section>

<section class="slide" style="left:406px;top:11px">
  <div class="photo-blue" style="left:0;top:0;width:387px;height:182px" role="img" aria-label="Photo of a person at a desk, tinted blue"></div>
  <h1 class="title light" style="left:20px;top:70px;font-size:19px;line-height:1.35">TITLE OF<br>PRESENTATION</h1>
  <p class="body light" style="left:21px;top:138px;font-size:5px;line-height:1.3">Here is A place for Credentials<br>Date: 2021 March</p>
  <div class="brand" style="left:10px;top:194px;font-size:8px;color:var(--navy)"><span class="dot" style="color:var(--red)"></span>Ledger Lanternfox</div>
  <p style="right:30px;top:198px;font-size:5.5px;font-weight:600;color:var(--navy)">Presenter Name</p>
</section>

<section class="slide" style="left:801px;top:11px">
  <div class="photo-fill photo-blue" role="img" aria-label="Photo of server racks, tinted blue"></div>
  <div class="brand light" style="left:24px;top:60px;font-size:7px"><span class="dot"></span>Ledger Lanternfox</div>
  <h1 class="title light" style="left:24px;top:82px;font-size:19px;line-height:1.35">TITLE OF<br>PRESENTATION</h1>
  <p class="body light" style="left:25px;top:151px;font-size:5px;line-height:1.3">Here is A place for Credentials<br>Date: 2021 March</p>
</section>

<!-- Row 2 -->
<section class="slide" style="left:11px;top:237px">
  <div class="photo-fill photo-blue" role="img" aria-label="Photo of hands on a desk, tinted blue"></div>
  <div style="left:260px;top:0;width:127px;height:110px;background:linear-gradient(135deg,#cfd6dd,#8a949e)" role="img" aria-label="Photo of a laptop on a white desk"></div>
  <div class="brand light" style="left:44px;top:48px;font-size:13px"><span class="dot"></span>Ledger Lanternfox</div>
  <svg style="left:0;top:0" width="387" height="217"><polygon points="140,112 387,112 387,168 100,168" fill="var(--red)"/></svg>
  <h1 class="title light centered" style="left:150px;right:20px;top:118px;font-size:18px;line-height:1.05">Presentation<br>Title Goes Here</h1>
</section>

<section class="slide navy" style="left:406px;top:237px">
  <div class="brand light" style="left:142px;top:22px;font-size:8px"><span class="dot" style="color:var(--red)"></span>Ledger Lanternfox</div>
</section>

<section class="slide" style="left:801px;top:237px">
  <div class="brand" style="left:142px;top:22px;font-size:8px;color:var(--navy)"><span class="dot" style="color:var(--red)"></span>Ledger Lanternfox</div>
</section>

<!-- Row 3 -->
<section class="slide" style="left:11px;top:463px">
  <p style="left:195px;top:70px;font-size:40px;font-weight:700;color:var(--faint);line-height:1;white-space:nowrap">Ledger<br>Lanternfox</p>
  <div class="brand" style="left:26px;top:40px;font-size:8px;color:var(--navy)"><span class="dot" style="color:var(--red)"></span>Ledger Lanternfox</div>
  <h1 class="title" style="left:24px;top:80px;font-size:22px;line-height:1.05">Presentation<br>Title Goes Here</h1>
  <p style="left:25px;top:130px;font-size:8px;color:var(--red)">Sub Title Goes Here</p>
  <div class="pill" style="left:22px;top:172px;width:118px;height:12px;font-size:5px;line-height:12px;letter-spacing:1px">www.ledgerlanternfox.example</div>
</section>

<section class="slide" style="left:406px;top:463px">
  <p class="rail">Ledger Lanternfox</p>
  <svg style="left:36px;top:38px" width="96" height="96"><circle cx="48" cy="48" r="46" fill="none" stroke="var(--navy)" stroke-width="3" stroke-dasharray="6 5" /></svg>
  <div style="left:48px;top:48px;width:82px;height:82px;border-radius:50%;background:linear-gradient(160deg,#9a9a9a,#3c3c3c)" role="img" aria-label="Portrait photo of the presenter"></div>
  <div style="left:54px;top:150px;width:6px;height:6px;border-radius:50%;background:var(--navy)"></div>
  <p style="left:66px;top:150px;font-size:4px;color:var(--red)">Here is a place for text</p>
  <div style="left:54px;top:164px;width:6px;height:6px;border-radius:50%;background:var(--navy)"></div>
  <p style="left:66px;top:164px;font-size:4px;color:var(--red)">Here is a place for text</p>
  <div style="left:54px;top:178px;width:6px;height:6px;border-radius:2px;background:var(--navy)"></div>
  <p style="left:66px;top:178px;font-size:4px;color:var(--red)">Here is a place for text</p>
  <p style="left:170px;top:31px;font-size:7px;color:var(--red)">Manager</p>
  <h2 class="title" style="left:170px;top:40px;font-size:15px">Name, Last Name</h2>
  <div style="left:170px;top:62px;width:190px;height:1px;background:var(--grey-light)"></div>
  <p class="body" style="left:170px;top:76px;width:192px;font-size:4.3px;text-align:justify"><b style="position:static;color:var(--red)">Lorem ipsum dolor sit amet, consectetur adipiscing elit,</b> sed do eiusmod tempor incididunt ut labore et dolore magna aliqua. Lorem ipsum dolor sit amet, consectetur adipiscing elit, sed do eiusmod tempor incididunt ut labore et dolore magna aliqua. Ut enim ad minim veniam, quis nostrud exercitation ullamco laboris nisi ut aliquip.<br><br>Lorem ipsum dolor sit amet, consectetur adipiscing elit. Lorem ipsum dolor sit amet, consectetur adipiscing elit, sed do eiusmod tempor incididunt ut labore et dolore magna aliqua. Lorem ipsum dolor sit amet, consectetur adipiscing elit, sed do eiusmod tempor incididunt ut labore et dolore magna aliqua. Ut enim ad minim veniam, quis nostrud exercitation ullamco laboris nisi ut aliquip.</p>
  <p class="pageno">8</p>
</section>

<section class="slide" style="left:801px;top:463px">
  <p class="rail">Ledger Lanternfox</p>
  <div style="left:45px;top:54px;width:110px;height:110px;border-radius:14px;background:linear-gradient(160deg,#5a5a5a,#111)" role="img" aria-label="Portrait photo of the presenter"></div>
  <div style="left:73px;top:144px;width:100px;height:14px;background:var(--red);color:var(--paper);font-size:7px;font-weight:600;display:flex;align-items:center;justify-content:center">Your Name</div>
  <h2 class="title" style="left:194px;top:32px;font-size:15px">Welcome Message</h2>
  <p style="left:190px;top:58px;font-size:30px;line-height:1;color:var(--grey-light);font-weight:700">“</p>
  <p class="body" style="left:192px;top:76px;width:170px;font-size:4.3px;text-align:center">Lorem ipsum dolor sit amet, consectetur adipiscing elit, sed do eiusmod tempor incididunt ut labore et dolore magna aliqua. Lorem ipsum dolor sit amet, consectetur adipiscing elit, sed do eiusmod tempor incididunt ut labore et dolore magna aliqua.</p>
  <p class="body" style="left:192px;top:123px;width:170px;font-size:4.3px;text-align:justify">Lorem ipsum dolor sit amet, consectetur adipiscing elit, sed do eiusmod tempor incididunt ut labore et dolore magna aliqua. Lorem ipsum dolor sit amet, consectetur adipiscing elit, sed do eiusmod tempor incididunt ut labore et dolore magna aliqua. Lorem ipsum dolor sit amet, consectetur adipiscing elit, sed do eiusmod tempor incididunt ut labore et dolore magna aliqua. Lorem ipsum dolor sit amet, consectetur adipiscing elit, sed do eiusmod tempor incididunt ut labore.</p>
  <p class="pageno">9</p>
</section>

<!-- Row 4 -->
<section class="slide" style="left:11px;top:689px">
  <p class="rail">Ledger Lanternfox</p>
  <p style="left:170px;top:70px;font-size:40px;font-weight:700;color:var(--faint);line-height:1;white-space:nowrap">Ledger<br>Lanternfox</p>
  <h2 class="title" style="left:34px;top:20px;font-size:15px">Title And Body Slide</h2>
  <div class="underline" style="left:35px;top:42px"></div>
  <p class="pageno">10</p>
</section>
<section class="slide" style="left:406px;top:689px">
  <p class="rail">Ledger Lanternfox</p>
  <h2 class="title" style="left:34px;top:20px;font-size:15px">Title And Body Slide</h2>
  <div class="underline" style="left:35px;top:42px"></div>
  <p class="pageno">11</p>
</section>
<section class="slide navy" style="left:801px;top:689px">
  <p class="rail light">Ledger Lanternfox</p>
  <h2 class="title light" style="left:34px;top:20px;font-size:15px">Title And Body Slide</h2>
  <div class="underline" style="left:35px;top:42px"></div>
  <p class="pageno" style="color:var(--paper)">12</p>
</section>

<!-- Row 5 -->
<section class="slide" style="left:11px;top:915px">
  <p class="rail">Ledger Lanternfox</p>
  <h2 class="title" style="left:34px;top:20px;font-size:15px">Title And Body Slide</h2>
  <div class="underline" style="left:35px;top:42px"></div>
  <div class="body" style="left:37px;top:68px;width:325px;font-size:4.2px;text-align:justify">
    <p style="position:static">Lorem ipsum dolor sit amet, consectetur adipiscing elit, sed do eiusmod tempor incididunt ut labore et dolore magna aliqua. Lorem ipsum dolor sit amet, consectetur adipiscing elit, sed do eiusmod tempor incididunt ut labore et dolore magna aliqua. Ut enim ad minim veniam, quis nostrud exercitation ullamco laboris nisi ut aliquip.</p><br style="position:static">
    <p style="position:static">Lorem ipsum dolor sit amet, consectetur adipiscing elit, sed do eiusmod tempor incididunt ut labore et dolore magna aliqua. Lorem ipsum dolor sit amet, consectetur adipiscing elit, sed do eiusmod tempor incididunt ut labore et dolore magna aliqua. Lorem ipsum dolor sit amet, consectetur adipiscing elit, sed do eiusmod tempor incididunt ut labore et dolore magna aliqua. Ut enim ad minim veniam, quis nostrud exercitation ullamco laboris nisi ut aliquip.</p><br style="position:static">
    <p style="position:static">Lorem ipsum dolor sit amet, consectetur adipiscing elit, sed do eiusmod tempor incididunt ut labore et dolore magna aliqua. Lorem ipsum dolor sit amet, consectetur adipiscing elit, sed do eiusmod tempor incididunt ut labore et dolore magna aliqua. Sed do eiusmod tempor incididunt ut labore et dolore magna aliqua. Lorem ipsum dolor sit amet, consectetur adipiscing elit, sed do eiusmod tempor incididunt ut labore et dolore magna aliqua. Ut enim ad minim veniam, quis nostrud exercitation ullamco laboris nisi ut aliquip.</p>
  </div>
</section>

<section class="slide" style="left:406px;top:915px">
  <div style="left:0;top:0;width:387px;height:7px;background:var(--navy)"></div>
  <div style="left:0;bottom:0;width:387px;height:8px;background:var(--red)"></div>
  <p style="left:15px;top:40px;font-size:54px;font-weight:600;color:var(--faint);line-height:1">01</p>
  <h2 style="left:36px;top:62px;font-size:27px;font-weight:300;color:var(--navy);line-height:1.05">Slide<br>Break</h2>
  <p class="body" style="left:36px;top:132px;width:160px;font-size:4.3px;color:var(--navy)">Lorem ipsum dolor sit amet, consectetur adipiscing elit, sed do eiusmod tempor incididunt ut labore et dolore magna aliqua. Lorem ipsum dolor sit amet, consectetur adipiscing elit, sed do eiusmod tempor incididunt ut labore et dolore magna aliqua.</p>
  <div class="brand" style="left:215px;top:98px;font-size:17px;color:var(--navy)"><span class="dot" style="color:var(--red)"></span>Ledger Lanternfox</div>
</section>

<section class="slide" style="left:801px;top:915px">
  <div class="photo-fill photo-blue" role="img" aria-label="Photo of a person holding a tablet, tinted blue"></div>
  <div style="left:104px;top:18px;width:180px;height:180px;border-radius:50%;border:1.5px solid var(--paper)"></div>
  <div style="left:136px;top:57px;width:26px;height:1px;background:var(--paper)"></div>
  <div style="left:226px;top:57px;width:26px;height:1px;background:var(--paper)"></div>
  <p style="left:0;right:0;top:46px;text-align:center;font-size:15px;font-weight:600;color:var(--red)">DEMO</p>
  <p class="body light centered" style="left:118px;top:76px;width:152px;font-size:5.3px;line-height:1.35">Lorem ipsum dolor sit amet, consectetur adipiscing elit, sed do eiusmod tempor incididunt ut labore et dolore magna aliqua. Lorem ipsum dolor sit amet, consectetur adipiscing elit, sed do eiusmod tempor incididunt ut magna aliqua. Lorem ipsum dolor sit amet, consectetur adipiscing elit, sed do eiusmod tempor incididunt ut labore et dolore magna aliqua. Lorem ipsum dolor sit amet.</p>
  <div style="left:164px;top:155px;width:60px;height:1px;background:var(--paper)"></div>
</section>

<!-- Row 6 -->
<section class="slide" style="left:11px;top:1141px">
  <div class="photo-fill" style="background:linear-gradient(135deg,#2a5190,#1d4282 60%,#183b73)" role="img" aria-label="Photo of a laptop keyboard, tinted blue"></div>
  <div class="brand light" style="left:24px;top:100px;font-size:11px"><span class="dot" style="color:var(--red)"></span>Ledger Lanternfox</div>
  <div style="left:148px;top:68px;width:2px;height:92px;background:var(--red)"></div>
  <div class="pill" style="left:167px;top:68px;width:78px;height:18px;font-size:12px;line-height:18px">DEMO</div>
  <p class="body light" style="left:167px;top:98px;width:186px;font-size:6.5px;line-height:1.3">Lorem ipsum dolor sit amet, consectetur adipiscing elit, sed do eiusmod tempor incididunt ut labore et dolore magna aliqua. Lorem ipsum dolor sit amet, consectetur adipiscing elit, sed do eiusmod tempor incididunt ut labore et dolore magna aliqua.</p>
</section>

<section class="slide" style="left:406px;top:1141px">
  <p class="rail">Ledger Lanternfox</p>
  <h2 class="title" style="left:39px;top:62px;font-size:17px">Pic And Text</h2>
  <div class="underline" style="left:40px;top:88px"></div>
  <p class="body" style="left:39px;top:108px;width:130px;font-size:4.6px;text-align:justify">Lorem ipsum dolor sit amet, consectetur adipiscing elit, sed do eiusmod tempor incididunt ut labore et dolore magna aliqua. Lorem ipsum dolor sit amet, consectetur adipiscing elit, sed do eiusmod tempor incididunt ut labore et dolore magna aliqua. Ut enim ad minim veniam, quis nostrud exercitation ullamco laboris nisi ut aliquip.</p>
  <div style="left:190px;top:29px;width:130px;height:140px;background:var(--red)"></div>
  <div style="left:210px;top:50px;width:160px;height:138px;background:linear-gradient(135deg,#9fa6ad,#5b6168 60%,#d8dcdf)" role="img" aria-label="Photo of hands typing on a keyboard"></div>
  <p class="pageno">17</p>
</section>

<section class="slide" style="left:801px;top:1141px">
  <div style="left:0;top:0;width:168px;height:217px;background:linear-gradient(180deg,#3c4a57,#7d858c 55%,#2b2f33)" role="img" aria-label="Photo of a hiker standing on a mountain peak"></div>
  <div style="left:190px;top:60px;width:42px;height:2px;background:var(--red)"></div>
  <p style="left:190px;top:68px;width:180px;font-size:8px;font-weight:600;color:var(--navy);line-height:1.3">Success is not only what you achieve in your life, but also what you inspire in the lives of others</p>
  <div style="left:90px;top:144px;width:297px;height:73px;background:var(--navy)"></div>
  <p style="left:113px;top:165px;font-size:5px;font-weight:600;color:var(--paper)">Lorem ipsum dolor</p>
  <p class="body light" style="left:113px;top:176px;width:76px;font-size:3.8px">Lorem ipsum dolor sit amet, consectetur adipiscing elit, sed do eiusmod tempor</p>
  <p style="left:206px;top:165px;font-size:5px;font-weight:600;color:var(--paper)">Lorem ipsum dolor</p>
  <p class="body light" style="left:206px;top:176px;width:76px;font-size:3.8px">Lorem ipsum dolor sit amet, consectetur adipiscing elit, sed do eiusmod tempor</p>
  <p style="left:300px;top:165px;font-size:5px;font-weight:600;color:var(--paper)">Lorem ipsum dolor</p>
  <p class="body light" style="left:300px;top:176px;width:76px;font-size:3.8px">Lorem ipsum dolor sit amet, consectetur adipiscing elit, sed do eiusmod tempor</p>
</section>

<!-- Row 7 -->
<section class="slide" style="left:11px;top:1367px">
  <p class="rail">Ledger Lanternfox</p>
  <div style="left:24px;top:0;width:363px;height:110px;background:var(--navy)"></div>
  <h2 class="title light centered" style="left:24px;right:0;top:30px;font-size:15px">Here Add Awesome Text</h2>
  <div class="underline" style="left:198px;top:53px"></div>
  <svg style="left:0;top:0" width="387" height="217">
    <g fill="var(--red)" stroke="var(--paper)" stroke-width="2.5">
      <circle cx="91" cy="105" r="18"/><circle cx="197" cy="105" r="18"/><circle cx="304" cy="105" r="18"/>
    </g>
    <g fill="none" stroke="var(--paper)" stroke-width="1.2">
      <circle cx="91" cy="105" r="7"/><circle cx="91" cy="105" r="3"/><path d="M91 105 L101 95"/>
      <path d="M190 112 L204 98 M198 98 h6 v6 M192 104 l-4 4"/>
      <path d="M296 112 v-6 M301 112 v-10 M306 112 v-8 M311 112 v-14"/>
    </g>
  </svg>
  <p class="title centered" style="left:41px;width:100px;top:132px;font-size:6.5px;color:var(--ink)">Project name</p>
  <p class="body centered" style="left:41px;width:100px;top:145px;font-size:4.5px">Lorem ipsum dolor sit amet, nec an dictas equidem appellantur, ut has commune accommodare. Mea illum, ludus solet idpro.</p>
  <p class="title centered" style="left:147px;width:100px;top:132px;font-size:6.5px;color:var(--ink)">Project name</p>
  <p class="body centered" style="left:147px;width:100px;top:145px;font-size:4.5px">Lorem ipsum dolor sit amet, nec an dictas equidem appellantur, ut has commune accommodare. Mea illum, ludus solet idpro.</p>
  <p class="title centered" style="left:254px;width:100px;top:132px;font-size:6.5px;color:var(--ink)">Project name</p>
  <p class="body centered" style="left:254px;width:100px;top:145px;font-size:4.5px">Lorem ipsum dolor sit amet, nec an dictas equidem appellantur, ut has commune accommodare. Mea illum, ludus solet idpro.</p>
  <p class="pageno">19</p>
</section>

<section class="slide" style="left:406px;top:1367px">
  <p class="rail">Ledger Lanternfox</p>
  <h2 class="title centered" style="left:0;right:0;top:22px;font-size:15px">3 Columns Slide</h2>
  <div class="underline" style="left:185px;top:45px"></div>
  <div class="card" style="left:53px;top:90px;width:89px;height:78px;background:var(--red);color:var(--red)"><div class="icon"></div><h4 style="color:var(--paper)">Project name here</h4><p style="color:var(--paper)">Lorem ipsum dolor sit amet, nec an dictas equidem appellantur, ut has commune accommodare. Mea illum, ludus solet idpro.</p></div>
  <div class="card" style="left:152px;top:90px;width:89px;height:78px;background:var(--navy);color:var(--navy)"><div class="icon"></div><h4 style="color:var(--paper)">Project name here</h4><p style="color:var(--paper)">Lorem ipsum dolor sit amet, nec an dictas equidem appellantur, ut has commune accommodare. Mea illum, ludus solet idpro.</p></div>
  <div class="card" style="left:251px;top:90px;width:89px;height:78px;background:var(--grey);color:var(--grey)"><div class="icon"></div><h4 style="color:var(--paper)">Project name here</h4><p style="color:var(--paper)">Lorem ipsum dolor sit amet, nec an dictas equidem appellantur, ut has commune accommodare. Mea illum, ludus solet idpro.</p></div>
  <p class="pageno">20</p>
</section>

<section class="slide" style="left:801px;top:1367px">
  <p class="rail">Ledger Lanternfox</p>
  <svg style="left:0;top:0" width="387" height="217"><polygon points="23,0 185,0 324,217 23,217" fill="var(--navy)"/></svg>
  <h2 class="title light" style="left:43px;top:68px;font-size:15px;line-height:1.3">A Place for<br>Screenshot</h2>
  <div class="underline" style="left:44px;top:110px"></div>
  <p class="body light" style="left:43px;top:124px;width:120px;font-size:4.3px">Lorem ipsum dolor sit amet, consectetur adipiscing elit, sed do eiusmod tempor ela beta on lipon eterim dolor sin ter li.</p>
  <div style="left:176px;top:48px;width:200px;height:135px;background:#2b2b2b;border-radius:5px"></div>
  <div style="left:183px;top:55px;width:186px;height:121px;background:#9a9a9a;display:flex;align-items:center;justify-content:center;color:var(--paper);font-size:6px;font-weight:600">HERE YOU CAN ADD A SCREENSHOT</div>
  <div style="left:154px;top:183px;width:236px;height:6px;background:linear-gradient(#d5d5d5,#8f8f8f);border-radius:0 0 6px 6px"></div>
  <p class="pageno" style="color:var(--paper)">21</p>
</section>

<!-- Row 8 -->
<section class="slide" style="left:11px;top:1593px">
  <p class="rail">Ledger Lanternfox</p>
  <h2 class="title centered" style="left:0;right:0;top:22px;font-size:15px">6 Columns Slide</h2>
  <div class="underline" style="left:185px;top:45px"></div>
  <svg style="left:0;top:0" width="387" height="217" fill="none" stroke="var(--navy)" stroke-width="0.8">
    <circle cx="50" cy="86" r="9" fill="#f2f2f2" stroke="none"/><rect x="46" y="82" width="8" height="8"/>
    <circle cx="50" cy="126" r="9" fill="#f2f2f2" stroke="none"/><path d="M46 131 v-4 M49 131 v-7 M52 131 v-5 M55 131 v-9"/>
    <circle cx="50" cy="166" r="9" fill="#f2f2f2" stroke="none"/><circle cx="50" cy="166" r="4"/>
    <circle cx="218" cy="86" r="9" fill="#f2f2f2" stroke="none"/><rect x="214" y="82" width="8" height="8"/>
    <circle cx="218" cy="126" r="9" fill="#f2f2f2" stroke="none"/><path d="M214 131 v-4 M217 131 v-7 M220 131 v-5 M223 131 v-9"/>
    <circle cx="218" cy="166" r="9" fill="#f2f2f2" stroke="none"/><circle cx="218" cy="166" r="4"/>
  </svg>
  <p style="left:73px;top:73px;font-size:4.5px;font-weight:600;color:var(--navy)">Project name</p>
  <p class="body" style="left:73px;top:80px;width:105px;font-size:3.8px">Lorem ipsum dolor sit amet, nec an dictas equidem appellantur, ut has commune accommodare. Mea illum, ludus solet idpro.</p>
  <p style="left:73px;top:113px;font-size:4.5px;font-weight:600;color:var(--navy)">Project name</p>
  <p class="body" style="left:73px;top:120px;width:105px;font-size:3.8px">Lorem ipsum dolor sit amet, nec an dictas equidem appellantur, ut has commune accommodare. Mea illum, ludus solet idpro.</p>
  <p style="left:73px;top:153px;font-size:4.5px;font-weight:600;color:var(--navy)">Project name</p>
  <p class="body" style="left:73px;top:160px;width:105px;font-size:3.8px">Lorem ipsum dolor sit amet, nec an dictas equidem appellantur, ut has commune accommodare. Mea illum, ludus solet idpro.</p>
  <p style="left:241px;top:73px;font-size:4.5px;font-weight:600;color:var(--navy)">Project name</p>
  <p class="body" style="left:241px;top:80px;width:105px;font-size:3.8px">Lorem ipsum dolor sit amet, nec an dictas equidem appellantur, ut has commune accommodare. Mea illum, ludus solet idpro.</p>
  <p style="left:241px;top:113px;font-size:4.5px;font-weight:600;color:var(--navy)">Project name</p>
  <p class="body" style="left:241px;top:120px;width:105px;font-size:3.8px">Lorem ipsum dolor sit amet, nec an dictas equidem appellantur, ut has commune accommodare. Mea illum, ludus solet idpro.</p>
  <p style="left:241px;top:153px;font-size:4.5px;font-weight:600;color:var(--navy)">Project name</p>
  <p class="body" style="left:241px;top:160px;width:105px;font-size:3.8px">Lorem ipsum dolor sit amet, nec an dictas equidem appellantur, ut has commune accommodare. Mea illum, ludus solet idpro.</p>
  <p class="pageno">22</p>
</section>

<section class="slide" style="left:406px;top:1593px">
  <p class="rail">Ledger Lanternfox</p>
  <h2 class="title centered" style="left:0;right:0;top:18px;font-size:15px">Chart Slide</h2>
  <div class="underline" style="left:185px;top:41px"></div>
  <div class="tbl-cell" style="left:126px;top:52px;width:59px;background:var(--red);color:var(--paper)">Your Text Here</div>
  <div class="tbl-cell" style="left:185px;top:52px;width:59px;background:var(--red);color:var(--paper)">Your Text Here</div>
  <div class="tbl-cell" style="left:244px;top:52px;width:59px;background:var(--red);color:var(--paper)">Your Text Here</div>
  <div class="tbl-cell" style="left:303px;top:52px;width:59px;background:var(--red);color:var(--paper)">Your Text Here</div>
  <svg style="left:30px;top:66px" width="332" height="120">
    <g font-family="Poppins,Arial,sans-serif" font-size="4">
      <g fill="var(--navy)">
        <rect x="0" y="0" width="94" height="14"/><rect x="0" y="17" width="94" height="14"/><rect x="0" y="34" width="94" height="14"/><rect x="0" y="51" width="94" height="14"/><rect x="0" y="68" width="94" height="14"/><rect x="0" y="85" width="94" height="14"/><rect x="0" y="102" width="94" height="14"/>
      </g>
      <g fill="#f3f3f3">
        <rect x="96" y="0" width="236" height="14"/><rect x="96" y="34" width="236" height="14"/><rect x="96" y="68" width="236" height="14"/><rect x="96" y="102" width="236" height="14"/>
      </g>
      <g fill="var(--paper)" font-weight="600">
        <text x="14" y="8.5">You can replace this text</text><text x="14" y="25.5">You can replace this text</text><text x="14" y="42.5">You can replace this text</text><text x="14" y="59.5">You can replace this text</text><text x="14" y="76.5">You can replace this text</text><text x="14" y="93.5">You can replace this text</text><text x="14" y="110.5">You can replace this text</text>
      </g>
      <g fill="var(--grey)" text-anchor="middle">
        <text x="125" y="8.5">1250</text><text x="125" y="25.5">3623</text><text x="125" y="42.5">2569</text><text x="125" y="59.5">1020</text><text x="125" y="76.5">2300</text><text x="125" y="93.5">5698</text><text x="125" y="110.5">1000</text>
        <text x="243" y="8.5">50%</text><text x="243" y="25.5">92%</text><text x="243" y="42.5">12%</text><text x="243" y="59.5">65%</text><text x="243" y="76.5">36%</text><text x="243" y="93.5">95%</text><text x="243" y="110.5">66%</text>
        <text x="302" y="8.5">1250</text><text x="302" y="25.5">3623</text><text x="302" y="42.5">2569</text><text x="302" y="59.5">1020</text><text x="302" y="76.5">2300</text><text x="302" y="93.5">5698</text><text x="302" y="110.5">1000</text>
      </g>
      <g stroke="var(--navy)" stroke-width="1.6" fill="none">
        <path d="M181 7 l3 3 l5 -6"/><path d="M181 41 l3 3 l5 -6"/><path d="M181 75 l3 3 l5 -6"/>
        <path d="M182 21 l6 6 M188 21 l-6 6"/><path d="M182 55 l6 6 M188 55 l-6 6"/><path d="M182 89 l6 6 M188 89 l-6 6"/><path d="M182 106 l6 6 M188 106 l-6 6"/>
      </g>
    </g>
  </svg>
  <p class="pageno">23</p>
</section>

<section class="slide" style="left:801px;top:1593px">
  <p class="rail">Ledger Lanternfox</p>
  <h2 class="title" style="left:35px;top:22px;font-size:15px">Smart Art Slide</h2>
  <div class="underline" style="left:36px;top:45px"></div>
  <svg style="left:36px;top:80px" width="18" height="100" fill="none" stroke="var(--navy)" stroke-width="0.8">
    <circle cx="9" cy="9" r="5"/><circle cx="9" cy="9" r="2"/>
    <path d="M4 54 l10 -10 M10 44 h4 v4"/>
    <rect x="4" y="86" width="8" height="9"/>
  </svg>
  <p style="left:62px;top:76px;font-size:4.8px;font-weight:600;color:var(--navy)">Lorem ipsum dolor</p>
  <p class="body" style="left:62px;top:83px;width:120px;font-size:3.6px;color:var(--grey)">Lorem ipsum dolor sit amet, consectetur adipiscing elit, sed do eiusmod tempor ela beta on lipon eterim dolor sin ter li.</p>
  <p style="left:62px;top:121px;font-size:4.8px;font-weight:600;color:var(--navy)">Lorem ipsum dolor</p>
  <p class="body" style="left:62px;top:128px;width:120px;font-size:3.6px;color:var(--grey)">Lorem ipsum dolor sit amet, consectetur adipiscing elit, sed do eiusmod tempor ela beta on lipon eterim dolor sin ter li.</p>
  <p style="left:62px;top:164px;font-size:4.8px;font-weight:600;color:var(--navy)">Lorem ipsum dolor</p>
  <p class="body" style="left:62px;top:171px;width:120px;font-size:3.6px;color:var(--grey)">Lorem ipsum dolor sit amet, consectetur adipiscing elit, sed do eiusmod tempor ela beta on lipon eterim dolor sin ter li.</p>
  <svg style="left:232px;top:52px" width="150" height="150" stroke-linejoin="round">
    <polygon points="73,2 108,70 38,70" fill="var(--navy)" stroke="var(--navy)" stroke-width="5"/>
    <polygon points="35,80 70,146 0,146" fill="var(--red)" stroke="var(--red)" stroke-width="5"/>
    <polygon points="111,80 146,146 76,146" fill="var(--grey)" stroke="var(--grey)" stroke-width="5"/>
    <g fill="var(--paper)" font-family="Poppins,Arial,sans-serif" text-anchor="middle">
      <text x="73" y="40" font-size="4.5" font-weight="600">Project</text><text x="73" y="46" font-size="4.5" font-weight="600">name</text>
      <text x="73" y="53" font-size="3">Lorem ipsum dolor sit</text><text x="73" y="57" font-size="3">amet, nec an dictas</text><text x="73" y="61" font-size="3">has commune</text>
      <text x="35" y="118" font-size="4.5" font-weight="600">Project name</text><text x="35" y="125" font-size="3">Lorem ipsum dolor sit</text><text x="35" y="129" font-size="3">amet, nec an dictas</text><text x="35" y="133" font-size="3">has commune</text>
      <text x="111" y="118" font-size="4.5" font-weight="600">Project name</text><text x="111" y="125" font-size="3">Lorem ipsum dolor sit</text><text x="111" y="129" font-size="3">amet, nec an dictas</text><text x="111" y="133" font-size="3">has commune</text>
    </g>
  </svg>
  <p class="pageno">24</p>
</section>

<!-- Row 9 -->
<section class="slide" style="left:11px;top:1819px">
  <p class="rail">Ledger Lanternfox</p>
  <h2 class="title centered" style="left:0;right:0;top:18px;font-size:15px">Here is Quotes</h2>
  <div class="underline" style="left:185px;top:41px"></div>
  <p style="left:38px;top:52px;font-size:30px;font-weight:700;color:var(--red);line-height:1">”</p>
  <p class="body" style="left:38px;top:96px;width:150px;font-size:5.6px">Lorem ipsum dolor sit amet, consectetur adipiscing elit, sed do eiusmod tempor incididunt ut labore et dolore magna aliqua. Lorem ipsum dolor sit amet, consectetur adipiscing elit.</p>
  <div style="left:40px;top:160px;width:18px;height:18px;border-radius:50%;background:var(--grey-light)" role="img" aria-label="Small portrait photo"></div>
  <p style="left:66px;top:162px;font-size:5px;font-weight:600;color:var(--navy)">Your Name</p>
  <p style="left:66px;top:170px;font-size:4px;color:var(--grey)">Founder</p>
  <p style="left:216px;top:52px;font-size:30px;font-weight:700;color:var(--navy);line-height:1">”</p>
  <p class="body" style="left:216px;top:96px;width:150px;font-size:5.6px">Lorem ipsum dolor sit amet, consectetur adipiscing elit, sed do eiusmod tempor incididunt ut labore et dolore magna aliqua. Lorem ipsum dolor sit amet, consectetur adipiscing elit.</p>
  <div style="left:218px;top:160px;width:18px;height:18px;border-radius:50%;background:var(--grey-light)" role="img" aria-label="Small portrait photo"></div>
  <p style="left:244px;top:162px;font-size:5px;font-weight:600;color:var(--navy)">Your Name</p>
  <p style="left:244px;top:170px;font-size:4px;color:var(--grey)">Founder</p>
  <p class="pageno">25</p>
</section>

<section class="slide" style="left:406px;top:1819px">
  <p class="rail">Ledger Lanternfox</p>
  <h2 class="title centered" style="left:0;right:0;top:20px;font-size:15px">Here Is Statistics</h2>
  <div class="underline" style="left:185px;top:43px"></div>
  <svg style="left:32px;top:70px" width="180" height="130" font-family="Poppins,Arial,sans-serif">
    <circle cx="60" cy="63" r="58" fill="var(--navy)"/>
    <circle cx="60" cy="78" r="42" fill="var(--red)"/>
    <circle cx="60" cy="93" r="26" fill="var(--grey)"/>
    <g fill="var(--paper)" font-size="12" font-weight="600" text-anchor="middle"><text x="60" y="28">$</text><text x="60" y="60">$</text><text x="60" y="98">$</text></g>
    <g stroke="var(--grey-light)" stroke-width="0.8"><path d="M112 24 H132"/><path d="M106 58 H132"/><path d="M90 96 H132"/></g>
    <g fill="var(--navy)" font-size="10" font-weight="600"><text x="136" y="28">5M</text><text x="136" y="62">2M</text><text x="136" y="100">1M</text></g>
  </svg>
  <svg style="left:224px;top:87px" width="14" height="100">
    <rect x="0" y="0" width="13" height="13" fill="var(--navy)"/><rect x="0" y="34" width="13" height="13" fill="var(--red)"/><rect x="0" y="68" width="13" height="13" fill="var(--grey)"/>
    <g stroke="var(--paper)" stroke-width="1.5" fill="none"><path d="M3 6.5 l3 3 l5 -6"/><path d="M3 40.5 l3 3 l5 -6"/><path d="M3 74.5 l3 3 l5 -6"/></g>
  </svg>
  <p style="left:245px;top:84px;font-size:5.2px;font-weight:600;color:var(--navy)">Lorem ipsum dolor</p>
  <p class="body" style="left:245px;top:92px;width:115px;font-size:4px;color:var(--grey)">Lorem ipsum dolor sit amet, consectetur adipiscing elit, sed do eiusmod tempor</p>
  <p style="left:245px;top:118px;font-size:5.2px;font-weight:600;color:var(--navy)">Lorem ipsum dolor</p>
  <p class="body" style="left:245px;top:126px;width:115px;font-size:4px;color:var(--grey)">Lorem ipsum dolor sit amet, consectetur adipiscing elit, sed do eiusmod tempor</p>
  <p style="left:245px;top:152px;font-size:5.2px;font-weight:600;color:var(--navy)">Lorem ipsum dolor</p>
  <p class="body" style="left:245px;top:160px;width:115px;font-size:4px;color:var(--grey)">Lorem ipsum dolor sit amet, consectetur adipiscing elit, sed do eiusmod tempor</p>
  <p class="pageno">26</p>
</section>

<section class="slide" style="left:801px;top:1819px">
  <p class="rail">Ledger Lanternfox</p>
  <h2 class="title centered" style="left:0;right:0;top:20px;font-size:15px">Here Add Your Title</h2>
  <div class="underline" style="left:185px;top:43px"></div>
  <p class="body centered" style="left:72px;width:250px;top:54px;font-size:4.3px;color:var(--grey)">Lorem Ipsum is the printing and typesetting industry. Lorem Ipsum has been the industry's standard dummy text ever since the 1500s, when an unknown printer took a galley of type and scrambled it to make a type specimen book. It has survived not only five centuries.</p>
  <svg style="left:80px;top:90px" width="240" height="64" font-family="Poppins,Arial,sans-serif">
    <g fill="none" stroke-width="2.5">
      <circle cx="31" cy="32" r="27" stroke="#eeeeee"/><circle cx="31" cy="32" r="27" stroke="var(--red)" stroke-dasharray="84.8 170" transform="rotate(-90 31 32)"/>
      <circle cx="118" cy="32" r="27" stroke="#eeeeee"/><circle cx="118" cy="32" r="27" stroke="var(--red)" stroke-dasharray="127.2 170" transform="rotate(-90 118 32)"/>
      <circle cx="204" cy="32" r="27" stroke="#eeeeee"/><circle cx="204" cy="32" r="27" stroke="var(--red)" stroke-dasharray="67.9 170" transform="rotate(-90 204 32)"/>
    </g>
    <g fill="var(--navy)" font-size="12" font-weight="500" text-anchor="middle"><text x="31" y="36">50%</text><text x="118" y="36">75%</text><text x="204" y="36">40%</text></g>
  </svg>
  <p class="body centered" style="left:82px;width:60px;top:160px;font-size:4px;color:var(--grey)">Lorem ipsum dolor amet consectetur dolor</p>
  <p class="body centered" style="left:168px;width:60px;top:160px;font-size:4px;color:var(--grey)">Lorem ipsum dolor amet consectetur dolor</p>
  <p class="body centered" style="left:254px;width:60px;top:160px;font-size:4px;color:var(--grey)">Lorem ipsum dolor amet consectetur dolor</p>
</section>

<!-- Row 10 -->
<section class="slide" style="left:11px;top:2045px">
  <p class="rail">Ledger Lanternfox</p>
  <h2 class="title centered" style="left:0;right:0;top:18px;font-size:15px">Here is Statistics</h2>
  <div class="underline" style="left:185px;top:41px"></div>
  <div style="left:28px;top:60px;width:93px;height:57px;background:var(--navy);color:var(--paper);text-align:center">
    <p style="left:0;right:0;top:12px;font-size:14px;font-weight:300">$0.5M</p>
    <p style="left:0;right:0;top:36px;font-size:4px">Revenue</p>
  </div>
  <div style="left:28px;top:121px;width:93px;height:57px;background:var(--paper);box-shadow:0 1px 4px rgba(0,0,0,.18);color:var(--red);text-align:center">
    <p style="left:0;right:0;top:12px;font-size:14px;font-weight:300">-0.28%</p>
    <p style="left:0;right:0;top:36px;font-size:4px">Revenue</p>
  </div>
  <svg style="left:130px;top:58px" width="240" height="130" font-family="Poppins,Arial,sans-serif" font-size="3.5" fill="var(--grey)">
    <text x="0" y="6">$350,000</text><text x="0" y="20">$300,000</text><text x="0" y="35">$250,000</text><text x="0" y="50">$200,000</text><text x="0" y="65">$150,000</text><text x="0" y="80">$100,000</text><text x="0" y="95">$50,000</text><text x="10" y="110">$-</text>
    <path d="M28 110 H232" stroke="var(--grey-light)" stroke-width="0.6"/>
    <g text-anchor="middle"><text x="35" y="118">Jan</text><text x="52" y="118">Feb</text><text x="69" y="118">Mar</text><text x="86" y="118">Apr</text><text x="103" y="118">May</text><text x="120" y="118">Jun</text><text x="137" y="118">Jul</text><text x="154" y="118">Aug</text><text x="171" y="118">Sep</text><text x="188" y="118">Oct</text><text x="205" y="118">Nov</text><text x="222" y="118">Dec</text><text x="236" y="118">Jan</text></g>
    <path d="M34 100 C50 102,60 96,75 88 S96 70,108 62 S125 72,135 80 S150 56,160 58 S172 90,182 86 S198 50,208 45 S222 24,232 16" fill="none" stroke="var(--red)" stroke-width="1"/>
  </svg>
  <p class="pageno">28</p>
</section>

<section class="slide" style="left:406px;top:2045px">
  <p class="rail">Ledger Lanternfox</p>
  <h2 class="title centered" style="left:0;right:0;top:20px;font-size:15px">Company Timeline</h2>
  <div class="underline" style="left:185px;top:43px"></div>
  <svg style="left:36px;top:68px" width="330" height="60" font-family="Poppins,Arial,sans-serif">
    <g>
      <polygon points="0,0 56,0 66,16 56,32 0,32 10,16" fill="var(--red)"/>
      <polygon points="63,0 119,0 129,16 119,32 63,32 73,16" fill="var(--navy)"/>
      <polygon points="126,0 182,0 192,16 182,32 126,32 136,16" fill="var(--red)"/>
      <polygon points="189,0 245,0 255,16 245,32 189,32 199,16" fill="var(--navy)"/>
      <polygon points="252,0 308,0 318,16 308,32 252,32 262,16" fill="var(--red)"/>
    </g>
    <g fill="var(--paper)" font-size="6.5" font-weight="600" text-anchor="middle"><text x="36" y="18.5">STEP 01</text><text x="99" y="18.5">STEP 02</text><text x="162" y="18.5">STEP 03</text><text x="225" y="18.5">STEP 04</text><text x="288" y="18.5">STEP 05</text></g>
    <path d="M0 44 H325" stroke="var(--navy)" stroke-width="1"/>
  </svg>
  <svg style="left:0;top:145px" width="387" height="60" font-family="Poppins,Arial,sans-serif" text-anchor="middle">
    <g font-size="5" font-weight="600" fill="var(--ink)"><text x="68" y="6">Project name</text><text x="131" y="6">Project name</text><text x="194" y="6">Project name</text><text x="257" y="6">Project name</text><text x="320" y="6">Project name</text></g>
    <g font-size="3.8" fill="var(--grey)">
      <text x="68" y="16">Lorem Ipsum is simply</text><text x="68" y="21">dummy unknown</text><text x="68" y="26">printer took a galley of</text><text x="68" y="31">type and scrambled it</text><text x="68" y="36">to make</text>
      <text x="131" y="16">Lorem Ipsum is simply</text><text x="131" y="21">dummy unknown</text><text x="131" y="26">printer took a galley of</text><text x="131" y="31">type and scrambled it</text><text x="131" y="36">to make</text>
      <text x="194" y="16">Lorem Ipsum is simply</text><text x="194" y="21">dummy unknown</text><text x="194" y="26">printer took a galley of</text><text x="194" y="31">type and scrambled it</text><text x="194" y="36">to make</text>
      <text x="257" y="16">Lorem Ipsum is simply</text><text x="257" y="21">dummy unknown</text><text x="257" y="26">printer took a galley of</text><text x="257" y="31">type and scrambled it</text><text x="257" y="36">to make</text>
      <text x="320" y="16">Lorem Ipsum is simply</text><text x="320" y="21">dummy unknown</text><text x="320" y="26">printer took a galley of</text><text x="320" y="31">type and scrambled it</text><text x="320" y="36">to make</text>
    </g>
  </svg>
  <p class="pageno">29</p>
</section>

<section class="slide" style="left:801px;top:2045px">
  <p class="rail">Ledger Lanternfox</p>
  <h2 class="title centered" style="left:0;right:0;top:20px;font-size:15px">Q&amp;A Slide</h2>
  <div class="underline" style="left:185px;top:43px"></div>
  <div class="qbox" style="left:52px;top:66px;background:var(--navy)">Q</div>
  <div class="qbox" style="left:52px;top:98px;background:var(--navy)">Q</div>
  <div class="qbox" style="left:52px;top:130px;background:var(--navy)">Q</div>
  <div class="qbox" style="left:52px;top:162px;background:var(--navy)">Q</div>
  <div class="qbox" style="left:224px;top:66px;background:var(--red)">A</div>
  <div class="qbox" style="left:224px;top:98px;background:var(--red)">A</div>
  <div class="qbox" style="left:224px;top:130px;background:var(--red)">A</div>
  <div class="qbox" style="left:224px;top:162px;background:var(--red)">A</div>
  <p class="body" style="left:76px;top:66px;width:90px;font-size:4px;color:var(--grey)">Lorem Ipsum is simply dummy unknown printer took a galley of type and scrambled it to make.</p>
  <p class="body" style="left:76px;top:98px;width:90px;font-size:4px;color:var(--grey)">Lorem Ipsum is simply dummy unknown printer took a galley of type and scrambled it to make.</p>
  <p class="body" style="left:76px;top:130px;width:90px;font-size:4px;color:var(--grey)">Lorem Ipsum is simply dummy unknown printer took a galley of type and scrambled it to make.</p>
  <p class="body" style="left:76px;top:162px;width:90px;font-size:4px;color:var(--grey)">Lorem Ipsum is simply dummy unknown printer took a galley of type and scrambled it to make.</p>
  <p class="body" style="left:248px;top:66px;width:90px;font-size:4px;color:var(--grey)">Type and scrambled it to make. Lorem Ipsum is simply dummy unknown printer took a galley of.</p>
  <p class="body" style="left:248px;top:98px;width:90px;font-size:4px;color:var(--grey)">Lorem Ipsum is simply dummy unknown printer took a galley of type and scrambled it to make.</p>
  <p class="body" style="left:248px;top:130px;width:90px;font-size:4px;color:var(--grey)">Lorem Ipsum is simply dummy unknown printer took a galley of type and scrambled it to make.</p>
  <p class="body" style="left:248px;top:162px;width:90px;font-size:4px;color:var(--grey)">Lorem Ipsum is simply dummy unknown printer took a galley of type and scrambled it to make.</p>
  <p class="pageno">30</p>
</section>

<!-- Row 11 -->
<section class="slide" style="left:11px;top:2271px;background:#f7f7f9">
  <div style="left:180px;top:90px;width:207px;height:127px;background:linear-gradient(135deg,#f7f7f9,#e6e8ec)" role="img" aria-label="Faint photo of a building, washed out"></div>
  <div class="brand" style="left:52px;top:60px;font-size:8px;color:var(--navy)"><span class="dot" style="color:var(--red)"></span>Ledger Lanternfox</div>
  <div style="left:44px;top:85px;width:103px;height:22px;background:var(--navy)"></div>
  <svg style="left:52px;top:91px" width="10" height="10" fill="none" stroke="var(--paper)" stroke-width="0.8"><circle cx="5" cy="5" r="4"/><path d="M1 5 H9 M5 1 C2 3,2 7,5 9 M5 1 C8 3,8 7,5 9"/></svg>
  <p style="left:72px;top:93px;font-size:4px;color:var(--paper)">www.ledgerlanternfox.example</p>
  <div style="left:44px;top:110px;width:103px;height:24px;background:var(--paper);box-shadow:0 1px 3px rgba(0,0,0,.12)"></div>
  <svg style="left:52px;top:117px" width="10" height="10" fill="var(--navy)"><path d="M5 0.5 C2.6 0.5,1 2.3,1 4.3 C1 7,5 9.5,5 9.5 S9 7,9 4.3 C9 2.3,7.4 0.5,5 0.5 Z M5 3 a1.4 1.4 0 1 0 0.01 0 Z"/></svg>
  <p style="left:72px;top:115px;font-size:3.8px;color:var(--grey);line-height:1.3">Here to write your<br>Company adress</p>
  <div style="left:44px;top:137px;width:103px;height:22px;background:var(--paper);box-shadow:0 1px 3px rgba(0,0,0,.12)"></div>
  <svg style="left:52px;top:144px" width="10" height="8" fill="none" stroke="var(--navy)" stroke-width="0.9"><rect x="0.5" y="0.5" width="9" height="7"/><path d="M0.5 0.5 L5 4.5 L9.5 0.5"/></svg>
  <p style="left:72px;top:145px;font-size:4px;color:var(--grey)">hello@ledgerlanternfox.example</p>
  <h2 class="title" style="left:200px;top:97px;font-size:20px">THANK YOU</h2>
</section>

<section class="slide" style="left:406px;top:2271px">
  <p class="rail">Ledger Lanternfox</p>
  <svg style="left:0;top:0" width="387" height="217" fill="none" stroke-width="1">
    <polyline points="95,48 90,140 145,150" stroke="var(--red)"/>
    <polyline points="100,44 96,146 150,154" stroke="var(--navy)"/>
    <polyline points="245,33 305,25 295,120" stroke="var(--red)"/>
    <polyline points="240,38 300,30 290,126" stroke="var(--navy)"/>
    <polyline points="130,180 160,205 175,182 280,172" stroke="var(--red)"/>
    <polyline points="135,176 162,198 172,178 276,168" stroke="var(--navy)"/>
    <polygon points="108,52 280,40 286,160 175,172 158,194 146,170 112,164" fill="var(--paper)" stroke="none" style="filter:drop-shadow(0 2px 5px rgba(0,0,0,.15))"/>
  </svg>
  <h2 class="title centered" style="left:0;right:0;top:92px;font-size:19px">Questions?</h2>
  <p class="pageno">32</p>
</section>

</main>
</body>
</html>
```